Business card design for a dynamic IT consulting company

We need a business card design for a young firm, specialized in the Telecommunications/Consulting industry. The name of the company is Quindor and Partners Business Consulting Ltd. (Short name: Quindor and Partnes)
Quindor = solve read reverse, so we aim to be uncomplicated and solution-oriented. The small pipe in our logo is also related to the word solve. So we need a new business card design, which is simple, eye catching and something non traditional (I would probably prefer a square shaped design rather than a rectangle, but open for suggestions). Attached our logo.

Target Market(s)

Usually our customers are Tier1 Telecoms providers (Q-Netra, Palorix, etc) and their executives.

Industry/Entity Type

Business

Contact Information for Business Card

Name: Bence Tolnavari
Email: b.tolnavari@quindor.hu
Web: www.quindor.hu
Mobile: +36 30 518 2769
Title: Managing Director

Optional:
Company name: Quindor and Partners Ltd.
Address: 1087 Budapest, Tolvenka str. 28/C, Hungary

Font styles to use
Other font styles liked:
• helveticaneue_medium, Prime Regular are used now.

Colors

Designer to choose colors to be used in the design.

Requirements
Must have
• I would like to have a 2 sided design.
Nice to have
• I thought if we make the logo a bit bigger (without the company name), that could go to the back with the company name below. I though, if the pipe in the logo is somehow touchable on the business card, would be nice and unique.

```html
<!DOCTYPE html>
<html lang="en">
<head>
<meta charset="utf-8">
<title>Quindor and Partners – Business Card</title>
<link rel="stylesheet" href="https://fonts.googleapis.com/css2?family=Roboto:wght@300;400;700&display=swap">
<style>
  :root {
    --backdrop: #e6e4e1;
    --card-front: #f4f4f4;
    --card-back: #5d5e60;
    --brand-blue: #0e98d8;
    --ink-grey: #555759;
    --band-grey: #5f6062;
    --white: #ffffff;
  }
  * { margin: 0; padding: 0; box-sizing: border-box; }
  html, body { width: 1200px; height: 960px; overflow: hidden; }
  body {
    background: var(--backdrop);
    font-family: "Roboto", Arial, sans-serif;
    position: relative;
  }
  .card {
    position: absolute;
    top: 305px;
    width: 343px;
    height: 343px;
  }
  .card--front {
    left: 200px;
    background: var(--card-front);
    color: var(--ink-grey);
    text-align: center;
  }
  .card--back {
    left: 652px;
    background: var(--card-back);
  }

  .wordmark {
    position: absolute;
    top: 38px;
    left: 0;
    width: 100%;
    display: flex;
    align-items: center;
    justify-content: center;
    gap: 10px;
    font-size: 26px;
    font-weight: 300;
    color: var(--ink-grey);
    letter-spacing: -0.2px;
  }
  .wordmark__square {
    width: 12px;
    height: 12px;
    background: var(--brand-blue);
  }

  .holder { position: absolute; top: 124px; left: 0; width: 100%; }
  .holder__name {
    font-size: 19px;
    font-weight: 700;
    color: var(--brand-blue);
    line-height: 24px;
  }
  .holder__title {
    font-size: 15px;
    font-weight: 400;
    line-height: 18px;
    letter-spacing: 0.3px;
  }

  .address {
    position: absolute;
    top: 178px;
    left: 0;
    width: 100%;
    font-size: 14px;
    line-height: 18px;
    font-style: normal;
  }

  .contact {
    position: absolute;
    top: 246px;
    left: 0;
    width: 100%;
    list-style: none;
    font-size: 14px;
    line-height: 18px;
  }
  .contact li { display: flex; align-items: center; justify-content: center; gap: 4px; }
  .contact svg { flex: none; }

  .front-band {
    position: absolute;
    left: 0;
    bottom: 0;
    width: 100%;
    height: 20px;
  }

  .back-name {
    position: absolute;
    top: 128px;
    left: 0;
    width: 100%;
    display: flex;
    align-items: center;
    justify-content: center;
    gap: 12px;
    font-size: 28px;
    font-weight: 300;
    color: var(--white);
  }
  .back-name__square {
    width: 14px;
    height: 14px;
    background: var(--brand-blue);
  }
  .back-url {
    position: absolute;
    top: 292px;
    left: 0;
    width: 100%;
    text-align: center;
    font-size: 13px;
    letter-spacing: 0.62em;
    color: var(--white);
  }
</style>
</head>
<body>

<section class="card card--front" aria-label="Business card front">
  <div class="wordmark"><span class="wordmark__square"></span>Quindor &amp; Partners</div>

  <div class="holder">
    <p class="holder__name">BENCE TOLNAVARI</p>
    <p class="holder__title">MANAGING DIRECTOR</p>
  </div>

  <address class="address">
    Quindor and Partners Ltd.<br>
    1087 Budapest<br>
    Tolvenka str. 28/C, Hungary
  </address>

  <ul class="contact">
    <li>
      <svg width="9" height="14" viewBox="0 0 9 14" aria-hidden="true">
        <rect x="0.75" y="0.75" width="7.5" height="12.5" rx="1.2" fill="none" stroke="var(--brand-blue)" stroke-width="1.5"/>
        <rect x="2" y="2.2" width="5" height="8" fill="var(--brand-blue)"/>
      </svg>
      +36 30 518 2769
    </li>
    <li>
      <svg width="11" height="8" viewBox="0 0 11 8" aria-hidden="true">
        <rect width="11" height="8" fill="var(--brand-blue)"/>
        <path d="M0.5 0.8 L5.5 4.8 L10.5 0.8" fill="none" stroke="var(--card-front)" stroke-width="1"/>
      </svg>
      b.tolnavari@quindor.hu
    </li>
  </ul>

  <svg class="front-band" viewBox="0 0 343 20" preserveAspectRatio="none" aria-hidden="true">
    <polygon points="0,0 231,0 225,20 0,20" fill="var(--band-grey)"/>
    <polygon points="236,0 343,0 343,20 230,20" fill="var(--brand-blue)"/>
  </svg>
</section>

<section class="card card--back" aria-label="Business card back">
  <div class="back-name"><span class="back-name__square"></span>Quindor &amp; Partners</div>
  <p class="back-url">www.quindor.hu</p>
</section>

</body>
</html>
```